Carpet cleaning company focused on high quality needs business cards

We are a growing company that just merged with another company and need to design a new business card. We do both residential as well as commercial cleaning. We do carpet, tile & grout, upholstery, hard floors, and stain & pet odor removal. We treat our customers like family and strive to achieve outstanding results with every job.

```html
<!DOCTYPE html>
<html lang="en">
<head>
<meta charset="UTF-8">
<title>Ridgeway Steam Cleaning – Business Cards</title>
<link href="https://fonts.googleapis.com/css2?family=Lato:wght@400;700;900&display=swap" rel="stylesheet">
<style>
  :root {
    --bg: #2a2a2b;
    --card: #ffffff;
    --card-shade: #ececec;
    --blue: #1477bd;
    --ink: #3a3a3a;
    --rule: #8a8a8a;
    --red: #e2463c;
    --navy: #1c2b3a;
    --tan: #b48a4e;
  }
  * { box-sizing: border-box; margin: 0; padding: 0; }
  html, body { width: 1200px; height: 900px; overflow: hidden; }
  body {
    background: var(--bg);
    font-family: "Lato", Arial, sans-serif;
    color: var(--ink);
    display: flex;
    flex-direction: column;
    align-items: center;
    justify-content: center;
    gap: 60px;
  }
  .card {
    width: 560px;
    height: 320px;
    border-radius: 26px;
    background: linear-gradient(135deg, var(--card-shade) 0%, var(--card) 55%);
    display: flex;
    align-items: center;
    padding: 0 34px;
  }
  .card__left { flex: 0 0 210px; display: flex; align-items: center; justify-content: center; }
  .card__divider { width: 1px; align-self: stretch; margin: 70px 24px; background: var(--rule); }
  .card__right { flex: 1; }

  /* Front card */
  .brand { display: flex; align-items: center; gap: 10px; }
  .brand__art {
    width: 96px; height: 96px;
    background: linear-gradient(160deg, var(--red) 0%, #c9362e 100%);
  }
  .brand__name {
    font-weight: 900; font-size: 21px; line-height: 1.05;
    color: var(--navy); text-transform: uppercase; width: 100px;
  }
  .section-title {
    color: var(--blue); font-weight: 900; font-size: 13px;
    text-transform: uppercase; letter-spacing: .3px; margin-bottom: 4px;
  }
  .services { list-style: none; font-size: 12.5px; line-height: 1.45; margin-bottom: 12px; }
  .services li::before { content: "\2731"; color: var(--blue); font-size: 9px; margin-right: 6px; vertical-align: 1px; }
  .hours { font-size: 12.5px; line-height: 1.45; }

  /* Back card */
  .hero-art {
    width: 200px; height: 220px;
    background: linear-gradient(160deg, var(--red) 0%, #c9362e 100%);
  }
  .owner-name { color: var(--blue); font-weight: 900; font-size: 17px; text-transform: uppercase; }
  .owner-role { font-size: 13px; margin-bottom: 8px; }
  .contacts { list-style: none; font-size: 12.5px; line-height: 1.5; }
  .contacts li { display: flex; align-items: flex-start; gap: 8px; }
  .contacts svg { flex: 0 0 13px; width: 13px; height: 13px; margin-top: 3px; fill: var(--blue); }
  .areas { display: flex; flex-direction: column; }
</style>
</head>
<body>

  <section class="card card--front">
    <div class="card__left">
      <div class="brand">
        <div class="brand__art" role="img" aria-label="Mascot illustration: a smiling cleaning technician holding a steam wand on a red square"></div>
        <div class="brand__name">Ridgeway Steam Cleaning</div>
      </div>
    </div>
    <div class="card__divider"></div>
    <div class="card__right">
      <h2 class="section-title">Our Services</h2>
      <ul class="services">
        <li>Natural Carpets</li>
        <li>Residential Carpet Cleaning</li>
        <li>Tile &amp; Grout</li>
        <li>Upholstery</li>
        <li>Hard Floors</li>
        <li>Dining Room And Office Chairs</li>
        <li>Stain &amp; Pet Odor Removal</li>
      </ul>
      <h2 class="section-title">Our Services Time</h2>
      <p class="hours">Mon.Tue.Wed.Thur.Fri- 9:00am - 6:00pm<br>Sat.Sun- Closed</p>
    </div>
  </section>

  <section class="card card--back">
    <div class="card__left">
      <div class="hero-art" role="img" aria-label="Large mascot illustration: cleaning technician with steam wand and hose on a red square"></div>
    </div>
    <div class="card__divider"></div>
    <div class="card__right">
      <h1 class="owner-name">Ridgeway Steam Care</h1>
      <p class="owner-role">Owner</p>
      <ul class="contacts">
        <li>
          <svg viewBox="0 0 24 24"><path d="M6.6 10.8a15.1 15.1 0 0 0 6.6 6.6l2.2-2.2a1 1 0 0 1 1-.25 11.4 11.4 0 0 0 3.6.57 1 1 0 0 1 1 1V20a1 1 0 0 1-1 1A17 17 0 0 1 3 4a1 1 0 0 1 1-1h3.5a1 1 0 0 1 1 1c0 1.25.2 2.45.57 3.57a1 1 0 0 1-.25 1z"/></svg>
          <span>(555) 014-2273</span>
        </li>
        <li>
          <svg viewBox="0 0 24 24"><path d="M2 5h20v14H2zm2 2v.4l8 5 8-5V7zm0 2.8V17h16V9.8l-8 5z"/></svg>
          <span>hello@ridgewaysteam.com</span>
        </li>
        <li>
          <svg viewBox="0 0 24 24"><path d="M12 2a10 10 0 1 0 0 20 10 10 0 0 0 0-20zm6.9 9h-3a15 15 0 0 0-1.4-6.3A8 8 0 0 1 18.9 11zM12 4.1c.9 1.2 1.8 3.6 1.9 6.9h-3.8c.1-3.3 1-5.7 1.9-6.9zM9.5 4.7A15 15 0 0 0 8.1 11h-3a8 8 0 0 1 4.4-6.3zM5.1 13h3a15 15 0 0 0 1.4 6.3A8 8 0 0 1 5.1 13zm6.9 6.9c-.9-1.2-1.8-3.6-1.9-6.9h3.8c-.1 3.3-1 5.7-1.9 6.9zm2.5-.6a15 15 0 0 0 1.4-6.3h3a8 8 0 0 1-4.4 6.3z"/></svg>
          <span>www.ridgewaysteam.com</span>
        </li>
        <li>
          <svg viewBox="0 0 24 24"><path d="M12 2a7 7 0 0 0-7 7c0 5.2 7 13 7 13s7-7.8 7-13a7 7 0 0 0-7-7zm0 9.5A2.5 2.5 0 1 1 12 6.5a2.5 2.5 0 0 1 0 5z"/></svg>
          <span class="areas">
            <span>Maple Falls, OH, US</span>
            <span>Cedar Grove, OH, US</span>
            <span>Brookhaven, OH, US</span>
            <span>North Linden, OH, US</span>
            <span>Fairmont, OH, US</span>
          </span>
        </li>
      </ul>
    </div>
  </section>

</body>
</html>
```